Wordpress template for a mens-choire webpage

Task is to design a Wordpress template for an 98 years old estonian mens choire webpage.
Design should involve details from the attached files, choire logo and the colors of the choire flag: in horizontal orientation bright sky-blue, white, bright grass-green.
Designer signature is allowed to be added to the template, with country of origin.

Reason: Deadline extended 2 days (until 2. March 2014) to accommodate designers creativity.

Thank you everyone for your great designs!
Our project has now entered into a voting and decision phase until 14th of March 2014 (included).

```html
<!DOCTYPE html>
<html lang="en">
<head>
<meta charset="utf-8">
<title>Kalda Men's Choir</title>
<link href="https://fonts.googleapis.com/css2?family=Open+Sans:wght@300;400;600;700&display=swap" rel="stylesheet">
<style>
  :root {
    --sky: #00b4ff;
    --royal: #0a47ff;
    --lime: #aaff00;
    --grass: #33ee00;
    --panel: #f6f6f6;
    --ink: #555555;
    --ink-soft: #8a8a8a;
    --event-red: #a31111;
    --event-mint: #9de8d6;
    --white: #ffffff;
  }
  * { box-sizing: border-box; margin: 0; padding: 0; }
  html, body { width: 945px; height: 1200px; overflow: hidden; }
  body {
    position: relative;
    background: var(--white);
    font-family: "Open Sans", sans-serif;
    font-weight: 300;
    color: var(--ink);
  }
  .bands { position: absolute; inset: 0; }
  .search {
    position: absolute; left: 682px; top: 28px; width: 166px; height: 18px;
    background: var(--white); border-radius: 2px;
    font-size: 9px; color: #aaa; padding: 3px 7px;
  }
  .page {
    position: absolute; left: 91px; top: 54px; width: 759px; height: 1066px;
    background: var(--panel);
  }
  .brand {
    position: absolute; left: 14px; top: 28px; width: 70px;
    display: flex; flex-direction: column; align-items: center; gap: 4px;
  }
  .brand-mark { width: 34px; height: 34px; border-radius: 50%; background: var(--event-red); }
  .brand-name { font-size: 9px; font-weight: 400; color: var(--ink); text-align: center; line-height: 1.15; }
  .main-nav {
    position: absolute; left: 103px; top: 45px;
    font-size: 13.5px; color: var(--ink); white-space: nowrap;
  }
  .main-nav span { margin: 0 4px; }
  .hero {
    position: absolute; left: 7px; top: 95px; width: 749px; height: 300px;
    background: linear-gradient(180deg, #6a2a0c 0%, #9a4a1a 40%, #2a1a14 75%, #c98a4a 100%);
  }
  .hero-title {
    position: absolute; left: 372px; top: 74px;
    font-size: 24px; color: var(--white); font-weight: 300; white-space: nowrap;
  }
  .hero-title strong { font-weight: 700; }
  .hero-arrow { position: absolute; top: 136px; }
  .thumbs { position: absolute; left: 7px; top: 417px; display: flex; gap: 10px; }
  .thumb { width: 243px; height: 109px; }
  .section-title { position: absolute; font-size: 14.5px; font-weight: 300; color: #666; }
  .event {
    position: absolute; left: 7px; width: 243px; height: 67px;
    background: var(--event-red); color: var(--white);
  }
  .event.muted { background: var(--event-mint); color: #f2fffb; }
  .event-day { position: absolute; left: 11px; top: 2px; font-size: 40px; font-weight: 300; line-height: 1.2; }
  .event-month { position: absolute; left: 12px; top: 49px; font-size: 10px; font-weight: 400; }
  .event-rule { position: absolute; left: 73px; top: 6px; width: 1px; height: 55px; background: currentColor; }
  .event-title { position: absolute; left: 84px; top: 15px; font-size: 10.5px; font-weight: 400; }
  .event-venue { position: absolute; left: 84px; top: 33px; font-size: 14px; font-weight: 400; }
  .media-item { position: absolute; top: 570px; width: 148px; }
  .media-still { position: relative; width: 147px; height: 148px; }
  .play { position: absolute; left: 52px; top: 52px; }
  .media-caption { margin-top: 14px; font-size: 11px; line-height: 16px; color: var(--ink); }
  .avatar {
    position: absolute; width: 106px; height: 106px; border-radius: 50%;
    border: 2px solid var(--white); box-shadow: 0 2px 3px rgba(0,0,0,.35);
  }
  .person-name { position: absolute; font-size: 14.5px; font-weight: 600; color: #666; white-space: nowrap; }
  .person-company { position: absolute; font-size: 11px; color: var(--ink-soft); white-space: nowrap; }
  .quote { position: absolute; top: 974px; width: 236px; font-size: 11px; line-height: 16px; color: var(--ink-soft); }
  .footer-nav {
    position: absolute; left: 0; top: 1138px; width: 945px; text-align: center;
    font-size: 11px; color: var(--ink); white-space: nowrap;
  }
  .footer-nav span { margin: 0 4px; }
  .copyright { position: absolute; left: 0; top: 1163px; width: 945px; text-align: center; font-size: 11px; color: var(--ink); }
</style>
</head>
<body>
  <svg class="bands" width="945" height="1200" viewBox="0 0 945 1200" aria-hidden="true">
    <polygon points="495,54 640,0 945,0 945,184 850,216 850,54" fill="var(--sky)"/>
    <polygon points="0,232 91,200 91,492 0,524" fill="var(--royal)"/>
    <polygon points="850,486 945,454 945,460 850,492" fill="#d0d0d0"/>
    <polygon points="850,492 945,460 945,760 850,792" fill="var(--lime)"/>
    <polygon points="0,794 91,766 91,772 0,800" fill="#d0d0d0"/>
    <polygon points="0,800 91,772 91,1068 0,1096" fill="var(--grass)"/>
  </svg>

  <div class="search">Search</div>

  <main class="page">
    <div class="brand">
      <span class="brand-mark"></span>
      <span class="brand-name">Kalda Men's Choir</span>
    </div>

    <nav class="main-nav">
      Watch &amp; Listen <span>&nbsp;|</span> Voices and the Quiet Hour <span>|</span> Events &amp; Tickets <span>|</span> Connect <span>|</span> About Us <span>|</span>Shop
    </nav>

    <section class="hero" role="img" aria-label="Photo of the men's choir singing on stage in a wood-panelled concert hall with a conductor">
      <h1 class="hero-title"><strong>98 Years</strong> of Estonian Choire</h1>
      <svg class="hero-arrow" style="left:10px" width="16" height="26" viewBox="0 0 16 26" aria-hidden="true"><polyline points="13,3 3,13 13,23" fill="none" stroke="#fff" stroke-width="3"/></svg>
      <svg class="hero-arrow" style="left:722px" width="16" height="26" viewBox="0 0 16 26" aria-hidden="true"><polyline points="3,3 13,13 3,23" fill="none" stroke="#fff" stroke-width="3"/></svg>
    </section>

    <div class="thumbs">
      <div class="thumb" role="img" aria-label="Choir and orchestra on a curved concert stage" style="background:linear-gradient(180deg,#8a6a5a,#3a2a24)"></div>
      <div class="thumb" role="img" aria-label="Choir members in black standing in a church" style="background:linear-gradient(180deg,#b8c4d0,#2a2a2e)"></div>
      <div class="thumb" role="img" aria-label="Large choir in rows on a golden-lit stage" style="background:linear-gradient(180deg,#e8e6df,#3a3328 60%,#e8b030)"></div>
    </div>

    <h2 class="section-title" style="left:7px;top:538px">Featured Event</h2>
    <h2 class="section-title" style="left:291px;top:538px">Media</h2>

    <article class="event" style="top:570px">
      <span class="event-day">23</span><span class="event-month">JAN 2014</span><span class="event-rule"></span>
      <span class="event-title">Voices and the Quiet Hour</span><span class="event-venue">Harbour Hall</span>
    </article>
    <article class="event" style="top:644px">
      <span class="event-day">23</span><span class="event-month">JAN 2014</span><span class="event-rule"></span>
      <span class="event-title">Voices and the Quiet Hour</span><span class="event-venue">Harbour Hall</span>
    </article>
    <article class="event muted" style="top:716px">
      <span class="event-day">23</span><span class="event-month">JAN 2014</span><span class="event-rule"></span>
      <span class="event-title">Voices and the Quiet Hour</span><span class="event-venue">Harbour Hall</span>
    </article>

    <article class="media-item" style="left:291px">
      <div class="media-still" role="img" aria-label="Video still of a youth choir in red jackets" style="background:linear-gradient(180deg,#d8d8d8,#a82030 50%,#2a2a2a)">
        <svg class="play" width="44" height="44" viewBox="0 0 44 44" aria-hidden="true"><circle cx="22" cy="22" r="20" fill="#555" fill-opacity=".8" stroke="#fff" stroke-width="2"/><polygon points="17,12 32,22 17,32" fill="#fff"/></svg>
      </div>
      <p class="media-caption">Neque porro quisquam est qui dolorem ipsum quia dolor sit amet, consectetur</p>
    </article>
    <article class="media-item" style="left:449px">
      <div class="media-still" role="img" aria-label="Video still of men's ensemble in black suits" style="background:linear-gradient(180deg,#e2e2e2,#3a3a3a 60%,#d0d0d0)">
        <svg class="play" width="44" height="44" viewBox="0 0 44 44" aria-hidden="true"><circle cx="22" cy="22" r="20" fill="#555" fill-opacity=".8" stroke="#fff" stroke-width="2"/><polygon points="17,12 32,22 17,32" fill="#fff"/></svg>
      </div>
      <p class="media-caption">Neque porro quisquam est qui dolorem ipsum quia dolor sit amet, consectetur</p>
    </article>
    <article class="media-item" style="left:607px">
      <div class="media-still" role="img" aria-label="Video still of women's choir outdoors on a lawn" style="background:linear-gradient(180deg,#6a8a4a,#2a2a2a 55%,#5aa830)">
        <svg class="play" width="44" height="44" viewBox="0 0 44 44" aria-hidden="true"><circle cx="22" cy="22" r="20" fill="#555" fill-opacity=".8" stroke="#fff" stroke-width="2"/><polygon points="17,12 32,22 17,32" fill="#fff"/></svg>
      </div>
      <p class="media-caption">Neque porro quisquam est qui dolorem ipsum quia dolor sit amet, consectetur</p>
    </article>

    <h2 class="section-title" style="left:7px;top:828px">Testimonials</h2>

    <div class="avatar" role="img" aria-label="Portrait photo of a reviewer" style="left:22px;top:853px;background:radial-gradient(circle,#c89070,#9a4a30)"></div>
    <p class="person-name" style="left:139px;top:878px">Arvo Linde</p>
    <p class="person-company" style="left:139px;top:898px">Company Name</p>
    <p class="quote" style="left:7px">Lorem Ipsum is simply dummy text of the printing and typesetting industry. Lorem Ipsum has been the industry's standard dummy</p>

    <div class="avatar" role="img" aria-label="Portrait photo of a reviewer" style="left:267px;top:853px;background:radial-gradient(circle,#e0b090,#e85a30 80%)"></div>
    <p class="person-name" style="left:380px;top:878px">Arvo Linde</p>
    <p class="person-company" style="left:380px;top:898px">Company Name</p>
    <p class="quote" style="left:263px">Lorem Ipsum is simply dummy text of the printing and typesetting industry. Lorem Ipsum has been the industry's standard dummy</p>

    <div class="avatar" role="img" aria-label="Portrait photo of a reviewer" style="left:514px;top:853px;background:radial-gradient(circle,#c89a80,#3a3a40 80%)"></div>
    <p class="person-name" style="left:626px;top:878px">Arvo Linde</p>
    <p class="person-company" style="left:626px;top:898px">Company Name</p>
    <p class="quote" style="left:520px">Lorem Ipsum is simply dummy text of the printing and typesetting industry. Lorem Ipsum has been the industry's standard dummy</p>
  </main>

  <nav class="footer-nav">
    Watch &amp; Listen <span>&nbsp;&nbsp;|</span> Voices and the Quiet Hour <span>|</span> Events &amp; Tickets <span>|</span> Connect <span>|</span> About Us <span>|</span>Shop
  </nav>
  <p class="copyright">© Copyright 2014 ,All Rights Reserved.</p>
</body>
</html>
```